Marta's Dwellings website

We need a simple website for our property investment business in the UK. We basically need our contact details and brief description.We have the company logo already done (via ArtFlockly) so please use these:https://drive.google.com/drive/folders/1szJ3iRhelElZ40NIFT7w-c14MaY3Y_oV?usp=sharingYou could use some stock photos of UK houses for now.Let me know when to provide more detailed descriptions, etc

Coding

Coded - Design and coding required

Number of Pages Required

1 page

Colors

Designer to choose colors to be used in the design.

```html
<!DOCTYPE html>
<html lang="en">
<head>
<meta charset="utf-8">
<title>Marta's Dwellings</title>
<link href="https://fonts.googleapis.com/css2?family=Montserrat:wght@300;400;500;600;700&display=swap" rel="stylesheet">
<style>
:root{
  --ink:#1d1d1d;
  --body:#555;
  --muted:#777;
  --band:#efefef;
  --white:#fff;
  --accent:#f08c00;
  --navy:#0e3b8c;
  --line:#bdbdbd;
}
*{box-sizing:border-box;margin:0;padding:0}
html,body{width:1200px;height:3014px;overflow:hidden}
body{position:relative;background:var(--white);font-family:'Montserrat',sans-serif;color:var(--ink)}
.abs{position:absolute}
.band{position:absolute;left:0;width:1200px}
.topbar{top:0;height:59px;background:var(--band)}
.topbar .phone{left:75px;top:20px;font-size:16px;font-weight:600;display:flex;align-items:center;gap:18px}
.follow{right:72px;top:18px;display:flex;align-items:center;gap:16px;font-size:13px;font-weight:600;letter-spacing:.5px}
.dot{display:inline-block;width:20px;height:20px;border-radius:50%;background:#777}
.nav{top:59px;height:105px;background:var(--white)}
.nav a{position:absolute;top:46px;font-size:16px;color:var(--ink);text-decoration:none;letter-spacing:.3px}
.brand{position:absolute;left:0;width:1200px;text-align:center;font-weight:400;color:var(--ink)}
.brand .mark{display:block;width:44px;height:44px;background:var(--ink);margin:0 auto 14px}
.brand .name{font-size:17px;letter-spacing:9px;padding-left:9px}
.hero{top:164px;height:574px;background:linear-gradient(180deg,#4a3a2c 0%,#6b4a36 35%,#5b3f30 65%,#2c3220 100%)}
.hero h1{position:absolute;left:0;width:1200px;text-align:center;color:#fff;font-weight:700;line-height:1}
.hero .l1{top:205px;font-size:52px}
.hero .l2{top:258px;font-size:68px}
.chev{position:absolute}
.section-title{position:absolute;left:0;width:1200px;text-align:center;font-size:44px;font-weight:400;letter-spacing:1px}
.photo{position:absolute}
.h2s{font-size:34px;font-weight:400;line-height:1.1}
.h2b{font-size:43px;font-weight:400;line-height:1.1}
.para{font-size:16px;line-height:27px;color:var(--body);font-weight:400}
.btn{position:absolute;border:1px solid var(--line);color:var(--accent);font-weight:700;font-size:14px;letter-spacing:.5px;display:flex;align-items:center;justify-content:center;background:#fff}
.card-title{position:absolute;text-align:center;font-size:19px;font-weight:700;letter-spacing:.5px}
.card-text{position:absolute;text-align:center;font-size:15px;line-height:23px;color:var(--body)}
.panel{position:absolute;left:75px;top:1291px;width:1052px;height:438px;background:#fff}
.foot-h{font-size:16px;font-weight:600;letter-spacing:.5px}
.small{font-size:13px;line-height:21px;color:var(--body)}
</style>
</head>
<body>

<!-- top bar -->
<div class="band topbar">
  <div class="abs phone">
    <svg width="14" height="14" viewBox="0 0 24 24"><path fill="#333" d="M6.6 10.8a15 15 0 0 0 6.6 6.6l2.2-2.2c.3-.3.7-.4 1-.2 1.1.4 2.3.6 3.6.6.6 0 1 .4 1 1V20c0 .6-.4 1-1 1A17 17 0 0 1 3 4c0-.6.4-1 1-1h3.5c.6 0 1 .4 1 1 0 1.3.2 2.5.6 3.6.1.3 0 .7-.2 1z"/></svg>
    1-800-555-0142
  </div>
  <div class="abs follow">FOLLOW US:
    <span class="dot" role="img" aria-label="Social link"></span>
    <span class="dot" role="img" aria-label="Social link"></span>
    <span class="dot" role="img" aria-label="Social link"></span>
    <span class="dot" role="img" aria-label="Social link"></span>
    <span class="dot" role="img" aria-label="Social link"></span>
  </div>
</div>

<!-- navigation -->
<div class="band nav">
  <a style="left:77px">HOME</a>
  <a style="left:174px">ABOUT US</a>
  <a style="left:300px">SERVICES</a>
  <div class="brand" style="top:-28px"><span class="mark"></span><span class="name">MARTA'S DWELLINGS</span></div>
  <a style="left:784px">PROPERTIES</a>
  <a style="left:925px">BLOG</a>
  <a style="left:1018px">CONTACT US</a>
</div>

<!-- hero -->
<div class="band hero" role="img" aria-label="Aerial view of a UK housing estate with red-brick homes among trees">
  <h1 class="l1">WELCOME TO</h1>
  <h1 class="l2">MARTA'S DWELLINGS</h1>
  <svg class="chev" style="left:74px;top:268px" width="22" height="36" viewBox="0 0 22 36"><path d="M18 3 4 18l14 15" fill="none" stroke="#fff" stroke-width="5"/></svg>
  <svg class="chev" style="left:1106px;top:268px" width="22" height="36" viewBox="0 0 22 36"><path d="M4 3l14 15L4 33" fill="none" stroke="#fff" stroke-width="5"/></svg>
</div>

<!-- about -->
<div class="photo" style="left:75px;top:792px;width:512px;height:323px;background:linear-gradient(135deg,#2c4d7a 0%,#8fb2d6 45%,#d9e8ec 70%,#6fa7ad 100%)" role="img" aria-label="Handshake over a model house and keys"></div>
<div class="abs" style="left:614px;top:803px">
  <div class="h2s">WELCOME TO</div>
  <div class="h2b">MARTA'S DWELLINGS</div>
</div>
<p class="abs para" style="left:614px;top:897px;width:480px">Lorem ipsum dolor sit amet, consectetur adipiscing elit. Integer vehicula, justo ut convallis auctor, justo eros pulvinar urna, in dignissim leo libero ut lorem. Proin malesuada dapibus enim, eu sollicitudin nunc efficitur vulputate. Donec consequat elit vel neque imperdiet euismod.</p>
<div class="btn" style="left:614px;top:1055px;width:179px;height:42px">READ MORE</div>

<!-- properties -->
<div class="band" style="top:1182px;height:599px;background:var(--band)"></div>
<div class="section-title" style="top:1222px">PROPERTIES</div>
<div class="panel"></div>
<div class="photo" style="left:92px;top:1314px;width:313px;height:196px;background:linear-gradient(180deg,#5b6e3a,#8a4a32 50%,#4f7a2e)" role="img" aria-label="Brick cottage with garden"></div>
<div class="photo" style="left:443px;top:1314px;width:314px;height:196px;background:linear-gradient(180deg,#8fa7c2,#a2533a 50%,#b39a7a)" role="img" aria-label="Red-brick detached house with driveway"></div>
<div class="photo" style="left:794px;top:1314px;width:314px;height:196px;background:linear-gradient(180deg,#7ea6d6,#b87356 55%,#6d8c3c)" role="img" aria-label="Row of new-build brick houses"></div>

<div class="card-title" style="left:75px;top:1534px;width:348px">SUSPENDISSE ID VIVERRA</div>
<div class="card-title" style="left:425px;top:1534px;width:350px">SUSPENDISSE ID VIVERRA</div>
<div class="card-title" style="left:777px;top:1534px;width:350px">SUSPENDISSE ID VIVERRA</div>
<p class="card-text" style="left:105px;top:1566px;width:290px">Curabitur aliquet felis nec euismod maximus. at tortor vulputate accumsa tempor leo ut sagittis.</p>
<p class="card-text" style="left:455px;top:1566px;width:290px">Curabitur aliquet felis nec euismod maximus. at tortor vulputate accumsa tempor leo ut sagittis.</p>
<p class="card-text" style="left:807px;top:1566px;width:290px">Curabitur aliquet felis nec euismod maximus. at tortor vulputate accumsa tempor leo ut sagittis.</p>
<div class="btn" style="left:165px;top:1654px;width:165px;height:42px">VIEW DETAILS</div>
<div class="btn" style="left:518px;top:1654px;width:165px;height:42px">VIEW DETAILS</div>
<div class="btn" style="left:869px;top:1654px;width:165px;height:42px">VIEW DETAILS</div>
<svg class="chev" style="left:45px;top:1499px" width="16" height="26" viewBox="0 0 16 26"><path d="M13 2 3 13l10 11" fill="none" stroke="#888" stroke-width="3"/></svg>
<svg class="chev" style="left:1141px;top:1499px" width="16" height="26" viewBox="0 0 16 26"><path d="M3 2l10 11L3 24" fill="none" stroke="#888" stroke-width="3"/></svg>

<!-- why choose -->
<div class="abs" style="left:75px;top:1847px">
  <div class="h2s">WHY CHOOSE</div>
  <div class="h2b">MARTA'S DWELLINGS</div>
</div>
<p class="abs para" style="left:75px;top:1940px;width:490px">Lorem ipsum dolor sit amet, consectetur adipiscing elit. Integer vehicula, justo ut convallis auctor, justo eros pulvinar urna, in dignissim leo libero ut lorem. Proin malesuada dapibus enim, eu sollicitudin nunc efficitur vulputate. Donec consequat elit vel neque imperdiet euismod.</p>
<div class="btn" style="left:75px;top:2098px;width:179px;height:43px">READ MORE</div>
<div class="photo" style="left:614px;top:1834px;width:513px;height:324px;background:linear-gradient(135deg,#e8e6e2 0%,#cfcac4 40%,#3a3f4a 60%,#eceae6 100%)" role="img" aria-label="Advisers meeting a client at an office table"></div>

<!-- blog -->
<div class="band" style="top:2216px;height:494px;background:var(--band)"></div>
<div class="section-title" style="top:2257px">BLOG POSTS</div>
<div class="photo" style="left:75px;top:2335px;width:330px;height:198px;background:linear-gradient(180deg,#8fb3dc,#9b4b35 55%,#6e8a3c)" role="img" aria-label="Brick house with conservatory"></div>
<div class="photo" style="left:433px;top:2335px;width:330px;height:198px;background:linear-gradient(180deg,#8f5a40,#a8503a 50%,#5c8a34)" role="img" aria-label="Red-brick house with garage"></div>
<div class="photo" style="left:795px;top:2335px;width:332px;height:198px;background:linear-gradient(180deg,#5d82c4,#9a4a36 55%,#4f7a2c)" role="img" aria-label="Detached brick family house"></div>
<div class="card-title" style="left:75px;top:2555px;width:330px">SUSPENDISSE ID VIVERRA</div>
<div class="card-title" style="left:433px;top:2555px;width:330px">SUSPENDISSE ID VIVERRA</div>
<div class="card-title" style="left:795px;top:2555px;width:332px">SUSPENDISSE ID VIVERRA</div>
<p class="card-text" style="left:95px;top:2586px;width:290px">Curabitur aliquet felis nec euismod maximus. at tortor vulputate accumsa tempor leo ut sagittis.</p>
<p class="card-text" style="left:453px;top:2586px;width:290px">Curabitur aliquet felis nec euismod maximus. at tortor vulputate accumsa tempor leo ut sagittis.</p>
<p class="card-text" style="left:816px;top:2586px;width:290px">Curabitur aliquet felis nec euismod maximus. at tortor vulputate accumsa tempor leo ut sagittis.</p>
<svg class="chev" style="left:45px;top:2533px" width="16" height="26" viewBox="0 0 16 26"><path d="M13 2 3 13l10 11" fill="none" stroke="#888" stroke-width="3"/></svg>
<svg class="chev" style="left:1141px;top:2533px" width="16" height="26" viewBox="0 0 16 26"><path d="M3 2l10 11L3 24" fill="none" stroke="#888" stroke-width="3"/></svg>

<!-- footer -->
<div class="abs" style="left:75px;top:2782px;width:206px;text-align:center">
  <span style="display:block;width:40px;height:40px;background:var(--ink);margin:0 auto 14px"></span>
  <span style="font-size:13px;letter-spacing:5px">MARTA'S DWELLINGS</span>
</div>
<p class="abs small" style="left:77px;top:2896px;font-size:12px;color:#333">Copyright © 2019. Company Name<br>All rights reserved.</p>

<div class="abs" style="left:422px;top:2764px;width:320px">
  <div class="foot-h">CONTACT INFO</div>
  <div style="color:var(--accent);font-weight:600;font-size:16px;margin-top:9px">Rosalind Vey</div>
  <p class="small" style="margin-top:8px">Unit 7, Orchard Court, 12-14 Millbrook Road,<br>Ashford Vale, Derbyshire,<br>United Kingdom, DE99 4QX</p>
  <div style="margin-top:12px;font-size:13px;font-weight:600;display:flex;align-items:center;gap:20px">
    <svg width="12" height="12" viewBox="0 0 24 24"><path fill="#333" d="M6.6 10.8a15 15 0 0 0 6.6 6.6l2.2-2.2c.3-.3.7-.4 1-.2 1.1.4 2.3.6 3.6.6.6 0 1 .4 1 1V20c0 .6-.4 1-1 1A17 17 0 0 1 3 4c0-.6.4-1 1-1h3.5c.6 0 1 .4 1 1 0 1.3.2 2.5.6 3.6.1.3 0 .7-.2 1z"/></svg>1-800-555-0142</div>
  <div style="margin-top:8px;font-size:13px;font-weight:600;display:flex;align-items:center;gap:20px">
    <svg width="13" height="11" viewBox="0 0 26 20"><rect x="1" y="1" width="24" height="18" fill="#333"/><path d="M1 1l12 10L25 1" fill="none" stroke="#fff" stroke-width="2"/></svg>info@martasdwellings-example.net</div>
</div>

<div class="abs" style="left:794px;top:2764px;width:333px">
  <div class="foot-h">NEWSLETTER SIGN UP</div>
  <p class="small" style="margin-top:9px;font-size:14px">Lorem ipsum dolor sit amet, consectetur adipiscing elit..</p>
</div>
<div class="abs" style="left:794px;top:2852px;width:242px;height:38px;border:1px solid #ccc;font-size:12px;color:var(--muted);padding:11px 13px">Enter Email Address</div>
<div class="abs" style="left:1036px;top:2852px;width:91px;height:38px;background:var(--navy);color:#fff;font-size:12px;font-weight:700;display:flex;align-items:center;justify-content:center;letter-spacing:.5px">SIGN UP</div>
<div class="abs" style="left:792px;top:2921px;display:flex;gap:20px">
  <span class="dot" style="background:#222" role="img" aria-label="Social link"></span>
  <span class="dot" style="background:#222" role="img" aria-label="Social link"></span>
  <span class="dot" style="background:#222" role="img" aria-label="Social link"></span>
  <span class="dot" style="background:#222" role="img" aria-label="Social link"></span>
  <span class="dot" style="background:#222" role="img" aria-label="Social link"></span>
</div>

</body>
</html>
```